Support People to improve their image and well-being by provided personalised advise

We need a design for business cards that could be used for production on plano press. We build a new business in our region for advising mostly women (also men though) on style embracing several aspects including fashion, style, self-confidence and ultimately your internal and external image. The business card should be "classy", "french-style". The business is located in the french -speaking part of Switzerland, close to France. The name of the company is Lomu Grace

Target Market(s)

Service fees won't be cheap (medium to premium) thus we target mid-class to upper-class women (1st target) and men (2nd target)

Industry/Entity Type

Life Coaching

Contact Information for Business Card

Conseil en Image

+41 76 418 63 07
tovasel@lomu-grace.example
linkedin.example/in/sel-moran-tova

Logo Text

Lomu Grace

Colors

Designer to choose colors to be used in the design.

```html
<!DOCTYPE html>
<html lang="fr">
<head>
<meta charset="utf-8">
<title>Lomu Grace – Cartes de visite</title>
<link href="https://fonts.googleapis.com/css2?family=Jost:wght@400;500&family=Kaushan+Script&display=swap" rel="stylesheet">
<style>
  :root {
    --backdrop: #c4c4c4;
    --card: #363a3d;
    --card-edge: #2c2f32;
    --gold-light: #e4c9a3;
    --gold-dark: #b88f62;
    --gold-text: #c9a070;
    --ink-light: #dcdcdc;
    --ink-soft: #c2c2c2;
  }
  * { margin: 0; padding: 0; box-sizing: border-box; }
  html, body {
    width: 1200px; height: 576px; overflow: hidden;
    background: var(--backdrop);
  }
  .sheet { position: relative; width: 1200px; height: 576px; }
  .card {
    position: absolute;
    border-radius: 14px;
    background: linear-gradient(180deg, var(--card) 0%, var(--card-edge) 100%);
    box-shadow: 0 2px 6px rgba(0,0,0,.25);
    overflow: hidden;
  }
  .card--front { left: 82px; top: 139px; width: 485px; height: 293px; }
  .card--back { left: 602px; top: 138px; width: 480px; height: 290px; }
  .brand {
    position: absolute; display: flex; flex-direction: column; align-items: center;
  }
  .card--front .brand { left: 0; width: 485px; top: 86px; }
  .card--back .brand { left: 40px; width: 180px; top: 92px; }
  .brand__dot {
    width: 62px; height: 62px; border-radius: 50%;
    background: linear-gradient(160deg, var(--gold-light), var(--gold-dark));
  }
  .brand__name {
    font-family: "Jost", sans-serif; font-weight: 500;
    color: var(--ink-light); letter-spacing: .16em; text-transform: uppercase;
    white-space: nowrap; line-height: 1.2;
  }
  .card--front .brand__name { font-size: 22px; margin-top: 29px; }
  .card--back .brand__name { font-size: 20px; margin-top: 23px; }
  .person { position: absolute; left: 270px; top: 86px; }
  .person__name {
    font-family: "Kaushan Script", cursive; font-size: 23px; color: var(--gold-text);
    white-space: nowrap;
  }
  .person__role {
    font-family: "Jost", sans-serif; font-size: 13px; color: var(--ink-soft); margin-top: 2px;
  }
  .contact { list-style: none; margin-top: 16px; }
  .contact__item {
    display: flex; align-items: center; gap: 14px; height: 18px;
    font-family: "Jost", sans-serif; font-size: 13px; color: var(--ink-soft);
    white-space: nowrap;
  }
  .contact__icon { width: 11px; height: 11px; fill: var(--ink-soft); flex: none; }
</style>
</head>
<body>
<main class="sheet">
  <section class="card card--front" aria-label="Recto">
    <div class="brand">
      <span class="brand__dot" aria-hidden="true"></span>
      <p class="brand__name">Lomu Grace</p>
    </div>
  </section>

  <section class="card card--back" aria-label="Verso">
    <div class="brand">
      <span class="brand__dot" aria-hidden="true"></span>
      <p class="brand__name">Lomu Grace</p>
    </div>
    <div class="person">
      <p class="person__name">Tova Sel Moran</p>
      <p class="person__role">Conseil en Image</p>
      <ul class="contact">
        <li class="contact__item">
          <svg class="contact__icon" viewBox="0 0 12 12" aria-hidden="true"><path d="M1 3.5C1 2 2.5 1.5 6 1.5S11 2 11 3.5v1H8.5V3.6H3.5v.9H1zM2.5 5.5h7L10.5 11h-9zM6 6.6a1.7 1.7 0 1 0 0 3.4 1.7 1.7 0 0 0 0-3.4z"/></svg>
          <span>+41 76 418 63 07</span>
        </li>
        <li class="contact__item">
          <svg class="contact__icon" viewBox="0 0 12 12" aria-hidden="true"><path d="M1 2.5h10v7H1zM1.6 3.1 6 6.6l4.4-3.5v.9L6 7.5 1.6 4z" fill-rule="evenodd"/></svg>
          <span>tovasel@lomu-grace.example</span>
        </li>
        <li class="contact__item">
          <svg class="contact__icon" viewBox="0 0 12 12" aria-hidden="true"><path d="M6 1a5 5 0 1 0 0 10A5 5 0 0 0 6 1zm0 1c.6.6 1.1 1.7 1.2 3.4H4.8C4.9 3.7 5.4 2.6 6 2zM2.1 5.4A4 4 0 0 1 4.2 2.4c-.4.8-.7 1.8-.7 3zm0 1.2h1.4c0 1.2.3 2.2.7 3a4 4 0 0 1-2.1-3zm2.7 0h2.4C7.1 8.3 6.6 9.4 6 10c-.6-.6-1.1-1.7-1.2-3.4zm3.7 0h1.4a4 4 0 0 1-2.1 3c.4-.8.7-1.8.7-3zm0-1.2c0-1.2-.3-2.2-.7-3a4 4 0 0 1 2.1 3z"/></svg>
          <span>www.lomu-grace.example</span>
        </li>
      </ul>
    </div>
  </section>
</main>
</body>
</html>
```